Business Card Design Project

This is to go hand in hand with our stationery project.
Target Market(s)
Business Professionals in the Finance, HR and C-Level management arena. They are global companies that run enterprise technology solutions/products.
Mostly Male, mid 30's to 60's.
Industry/Entity Type
Business
Font styles to use
Other font styles liked:
- Calibri
Colors
9bcb3c
000000
1b1b1b
c4c4c4
ffffff
Requirements
Must have
- Logo
Name, title, contact details, address on the front of the card.
ABN and web address need to be on the card, along with our tag line
See | Share | Do
We also require rounded corners and for the card to be landscape please.
Our green is
C98 M0 Y93 K0
Modern, contemporary and must have white space for people to write on.
Nice to have
- Consistent elements with the stationery design.
Should not have
- No 90's waves - We want the feeling of movement but no wavey lines.

```html
<!DOCTYPE html>
<html lang="en">
<head>
<meta charset="utf-8">
<title>Norvale Business Solutions – Business Cards</title>
<link rel="stylesheet" href="https://fonts.googleapis.com/css2?family=Carlito:wght@400;700&display=swap">
<style>
  :root {
    --green: #6cc04a;
    --panel: #3c3c3c;
    --ink: #1b1b1b;
    --grey: #c4c4c4;
    --paper: #ffffff;
    --backdrop: #dcd8d3;
    --font: "Carlito", sans-serif;
  }
  * { box-sizing: border-box; margin: 0; padding: 0; }
  html, body { width: 1200px; height: 914px; overflow: hidden; }
  body { background: var(--backdrop); font-family: var(--font); position: relative; }

  .card {
    position: absolute;
    width: 620px;
    height: 380px;
    border-radius: 16px;
    background: var(--paper);
    overflow: hidden;
    box-shadow: 0 6px 18px rgba(0,0,0,0.18);
  }
  .card--back { left: 520px; top: 60px; }
  .card--front { left: 60px; top: 474px; display: flex; }

  /* brand name stand-in */
  .brand__name { font-weight: 700; color: var(--ink); line-height: 1; }

  /* back */
  .back__center {
    position: absolute; inset: 0;
    display: flex; flex-direction: column; align-items: center; justify-content: center; gap: 26px;
  }
  .card--back .brand__name { font-size: 58px; }
  .tagline { display: flex; align-items: center; gap: 22px; font-size: 20px; color: var(--ink); }
  .tagline__divider { width: 1px; height: 30px; background: var(--ink); }

  /* front */
  .front__brand-side {
    width: 43%; display: flex; align-items: center; justify-content: center;
  }
  .card--front .brand__name { font-size: 44px; }
  .front__details {
    width: 57%; background: var(--panel); color: var(--paper);
    padding: 34px 16px 0 28px;
  }
  .company { color: var(--green); font-size: 24px; font-weight: 400; line-height: 1; white-space: nowrap; }
  .abn { font-size: 18px; margin-top: 6px; }
  .contact-list { list-style: none; margin-top: 30px; display: flex; flex-direction: column; gap: 9px; }
  .contact-list li { display: flex; align-items: flex-start; gap: 16px; font-size: 19px; line-height: 1.15; }
  .contact-list svg { width: 18px; height: 18px; flex: none; margin-top: 1px; fill: var(--paper); }
</style>
</head>
<body>

<section class="card card--back" aria-label="Card back">
  <div class="back__center">
    <p class="brand__name">Norvale</p>
    <p class="tagline">
      <span>Plan</span><span class="tagline__divider"></span>
      <span>Build</span><span class="tagline__divider"></span>
      <span>Grow</span>
    </p>
  </div>
</section>

<section class="card card--front" aria-label="Card front">
  <div class="front__brand-side">
    <p class="brand__name">Norvale</p>
  </div>
  <div class="front__details">
    <h1 class="company">Norvale Business Solutions</h1>
    <p class="abn">ABN: 48 213 507 926</p>
    <ul class="contact-list">
      <li>
        <svg viewBox="0 0 24 24" aria-hidden="true"><path d="M6.6 10.8a15.1 15.1 0 0 0 6.6 6.6l2.2-2.2c.3-.3.7-.4 1-.2 1.1.4 2.3.6 3.6.6.6 0 1 .4 1 1V20c0 .6-.4 1-1 1A17 17 0 0 1 3 4c0-.6.4-1 1-1h3.5c.6 0 1 .4 1 1 0 1.3.2 2.5.6 3.6.1.3 0 .7-.2 1z"/></svg>
        <span>+61 2 9000 4172</span>
      </li>
      <li>
        <svg viewBox="0 0 24 24" aria-hidden="true"><path d="M7 3h8l2 2v4H7zM4 10h16a2 2 0 0 1 2 2v6h-4v3H6v-3H2v-6a2 2 0 0 1 2-2zm4 6v3h8v-3z"/></svg>
        <span>+61 2 9000 4185</span>
      </li>
      <li>
        <svg viewBox="0 0 24 24" aria-hidden="true"><path d="M12 2a7 7 0 0 0-7 7c0 5.2 7 13 7 13s7-7.8 7-13a7 7 0 0 0-7-7zm0 9.5a2.5 2.5 0 1 1 0-5 2.5 2.5 0 0 1 0 5z"/></svg>
        <span>Level 6, 42 Harbour Lane,<br>Northbridge NSW 2063</span>
      </li>
      <li>
        <svg viewBox="0 0 24 24" aria-hidden="true"><path d="M2 5h20v14H2zm2 2v.5l8 5.5 8-5.5V7zm0 3v7h16v-7l-8 5.5z"/></svg>
        <span>Sales@norvalebiz.com</span>
      </li>
      <li>
        <svg viewBox="0 0 24 24" aria-hidden="true"><path d="M12 2a10 10 0 1 0 0 20 10 10 0 0 0 0-20zm6.9 6h-3a15 15 0 0 0-1.3-3.9A8 8 0 0 1 18.9 8zM12 4c.8 1.2 1.5 2.5 1.9 4h-3.8c.4-1.5 1.1-2.8 1.9-4zM4.3 14a8 8 0 0 1 0-4h3.4a16 16 0 0 0 0 4zm.8 2h3a15 15 0 0 0 1.3 3.9A8 8 0 0 1 5.1 16zm3-8h-3a8 8 0 0 1 4.3-3.9A15 15 0 0 0 8.1 8zM12 20c-.8-1.2-1.5-2.5-1.9-4h3.8c-.4 1.5-1.1 2.8-1.9 4zm2.3-6H9.7a14 14 0 0 1 0-4h4.6a14 14 0 0 1 0 4zm.3 5.9a15 15 0 0 0 1.3-3.9h3a8 8 0 0 1-4.3 3.9zm1.7-5.9a16 16 0 0 0 0-4h3.4a8 8 0 0 1 0 4z"/></svg>
        <span>www.norvalebiz.com</span>
      </li>
    </ul>
  </div>
</section>

</body>
</html>
```